Harbor Crestline (Business Card Design)

Need business cards designed. Something modern, chic, and sleek. Mabye the back of the card should be the navy blue that is in the logo and then just the logo on the back.

Target Market(s)

Those in the hotel, office, and renovation industry

Contact Information for Business Card

1. Logo 2. Dorian Fenwick 3. CEO/Founder 4. Phone: (833) HarbCre / (833) 427-2731 5. Email: dorian@theharborcrestline.com 6. Website: www.theharborcrestline.com

Font styles to use
Other font styles liked:
• Look at the logo font and base the font for everything else off of that.

Colors
0054AA
0677BA
7BADD7
CADEEF
E8F1F8

Requirements
Must have
• Colors that are associated in the logo
Nice to have
• Sleek modern clean and chic design.

```html
<!DOCTYPE html>
<html lang="en">
<head>
<meta charset="utf-8">
<title>Harbor Crestline – Business Card</title>
<link rel="stylesheet" href="https://fonts.googleapis.com/css2?family=Montserrat:wght@500;600;700;800&family=Open+Sans:wght@400;600&display=swap">
<style>
  :root {
    --backdrop: #1e1f24;
    --navy-deep: #0b1446;
    --navy: #141f62;
    --navy-light: #1f2c7a;
    --gold: #c9a24a;
    --ink: #111111;
    --paper: #ffffff;
    --logo-text: #ffffff;
  }
  * { box-sizing: border-box; margin: 0; padding: 0; }
  html, body {
    width: 1200px; height: 780px; overflow: hidden;
    background: var(--backdrop);
  }
  .stage {
    width: 1200px; height: 780px;
    display: flex; align-items: center; justify-content: center; gap: 40px;
  }
  .card {
    position: relative;
    width: 540px; height: 310px;
    border-bottom: 5px solid var(--gold);
    overflow: hidden;
  }

  /* Back side */
  .card--back {
    background: var(--navy);
  }
  .card__pattern {
    position: absolute; inset: 0;
    background: linear-gradient(200deg, var(--navy-light) 0%, var(--navy) 45%, var(--navy-deep) 100%);
  }
  .brand {
    position: absolute; right: 34px; bottom: 40px;
    display: flex; align-items: center; gap: 10px;
  }
  .brand__mark {
    width: 18px; height: 18px; border: 2px solid var(--logo-text);
  }
  .brand__name {
    font-family: "Montserrat", sans-serif;
    font-weight: 600; font-size: 17px; letter-spacing: 1.5px;
    text-transform: uppercase; color: var(--logo-text);
  }

  /* Front side */
  .card--front {
    background: var(--paper);
    color: var(--ink);
  }
  .identity {
    position: absolute; left: 60px; top: 92px;
    text-align: right; width: 210px;
  }
  .identity__name {
    font-family: "Montserrat", sans-serif;
    font-weight: 800; font-size: 30px; line-height: 1.05;
  }
  .identity__first { color: var(--gold); }
  .identity__last { color: var(--ink); }
  .identity__title {
    font-family: "Open Sans", sans-serif;
    font-size: 15px; margin-top: 4px;
  }
  .divider {
    position: absolute; left: 292px; top: 70px;
    width: 2px; height: 108px; background: var(--ink);
  }
  .contacts {
    position: absolute; left: 310px; top: 90px;
    list-style: none;
    font-family: "Open Sans", sans-serif; font-size: 11.5px; line-height: 1;
  }
  .contacts li {
    display: flex; align-items: center; gap: 7px; margin-bottom: 11px;
    white-space: nowrap;
  }
  .contacts svg { width: 12px; height: 12px; flex: none; }
  .address {
    position: absolute; left: 0; right: 0; bottom: 40px;
    text-align: center;
    font-family: "Open Sans", sans-serif; font-size: 15px;
  }
</style>
</head>
<body>
<main class="stage">

  <section class="card card--back" aria-label="Card back">
    <div class="card__pattern" role="img" aria-label="Navy background with a repeating tonal brand pattern"></div>
    <div class="brand">
      <span class="brand__mark"></span>
      <span class="brand__name">Harbor Crestline</span>
    </div>
  </section>

  <section class="card card--front" aria-label="Card front">
    <div class="identity">
      <h1 class="identity__name"><span class="identity__first">Dorian</span> <span class="identity__last">Fenwick</span></h1>
      <p class="identity__title">CEO/Founder</p>
    </div>
    <span class="divider"></span>
    <ul class="contacts">
      <li>
        <svg viewBox="0 0 24 24" aria-hidden="true"><path fill="#c9a24a" d="M6.6 10.8a15.1 15.1 0 0 0 6.6 6.6l2.2-2.2a1 1 0 0 1 1-.25 11.4 11.4 0 0 0 3.6.57 1 1 0 0 1 1 1V20a1 1 0 0 1-1 1A17 17 0 0 1 3 4a1 1 0 0 1 1-1h3.5a1 1 0 0 1 1 1c0 1.25.2 2.45.57 3.57a1 1 0 0 1-.25 1z"/></svg>
        (833) HarbCre / (833) 427-2731
      </li>
      <li>
        <svg viewBox="0 0 24 24" aria-hidden="true"><circle cx="12" cy="12" r="9" fill="none" stroke="#c9a24a" stroke-width="2.5"/><path d="M3 12h18M12 3c3 3 3 15 0 18M12 3c-3 3-3 15 0 18" fill="none" stroke="#c9a24a" stroke-width="2"/></svg>
        www.theharborcrestline.com
      </li>
      <li>
        <svg viewBox="0 0 24 24" aria-hidden="true"><rect x="2" y="5" width="20" height="14" rx="2" fill="#c9a24a"/><path d="M3 6l9 7 9-7" fill="none" stroke="#ffffff" stroke-width="2"/></svg>
        dorian@theharborcrestline.com
      </li>
    </ul>
    <p class="address">4120 Linden Park Rd Suite 210, Ashford, MD 21090</p>
  </section>

</main>
</body>
</html>
```